Sales Page Header Design Project

Hi,
I need a background image created for this sales page: http://trimventurecamp.com
Width: 977 px
Height: 150 px
Here are a few sample designs to work with: http://firmsummitschool.com/
http://craftingamarkweb.com/wp-content/uploads/2011/02/experts1.png
Must be sharp, professional looking and uncluttered.
Colours: Must include blue (I like the blue on the on the current sales page, but will leave shade and colour combinations to your creativity)
Text = Tobi Wanrenu Presents
Trim Venture Camp
Your Blueprint for Building a Profitable, Sustainable Business in Today's Economy!
Any questions, give me a shout
Entrepreneurs and Business Owners, aged 21 to 45
Business

```html
<!DOCTYPE html>
<html lang="en">
<head>
<meta charset="utf-8">
<title>Trim Venture Camp – Sales Page Header</title>
<link rel="stylesheet" href="https://fonts.googleapis.com/css2?family=Arimo:ital,wght@0,400;0,700;1,400&display=swap">
<style>
  :root {
    --page-bg: #f4f4f4;
    --band-edge: #0b2a40;
    --band-mid: #1f6494;
    --band-glow: #3289c4;
    --text-white: #ffffff;
    --tagline-cyan: #2fd3f0;
    --mark-blue: #3aa8e0;
  }
  html, body {
    margin: 0;
    padding: 0;
    width: 1200px;
    height: 1000px;
    overflow: hidden;
    background: var(--page-bg);
  }
  .header-band {
    position: absolute;
    left: 109px;
    top: 388px;
    width: 977px;
    height: 150px;
    background: radial-gradient(ellipse 60% 120% at 50% 0%, var(--band-glow) 0%, var(--band-mid) 45%, var(--band-edge) 100%);
    font-family: "Arimo", Arial, sans-serif;
    color: var(--text-white);
    text-align: center;
  }
  .presenter {
    position: absolute;
    top: 22px;
    left: 0;
    right: 0;
    font-size: 16px;
    letter-spacing: 0.2px;
  }
  .presenter .presents {
    font-size: 9px;
    letter-spacing: 1.5px;
    margin-left: 2px;
  }
  .brand-line {
    position: absolute;
    top: 54px;
    left: 0;
    right: 0;
    display: flex;
    justify-content: center;
    align-items: center;
    gap: 16px;
  }
  .brand-name {
    font-size: 56px;
    font-weight: 400;
    line-height: 60px;
    color: var(--text-white);
  }
  .brand-square {
    width: 26px;
    height: 26px;
    background: var(--mark-blue);
  }
  .tagline {
    position: absolute;
    top: 114px;
    left: 0;
    right: 0;
    font-size: 16px;
    font-style: italic;
    color: var(--tagline-cyan);
    letter-spacing: 0.3px;
  }
</style>
</head>
<body>
  <header class="header-band">
    <p class="presenter" style="margin:0">Tobi Wanrenu <span class="presents">Presents</span></p>
    <div class="brand-line">
      <span class="brand-square" aria-hidden="true"></span>
      <h1 class="brand-name" style="margin:0">Trim Venture Camp</h1>
    </div>
    <p class="tagline" style="margin:0">Your Blueprint for Building a Profitable, Sustainable Business in Today's Economy!</p>
  </header>
</body>
</html>
```